Maple Roster Business Card for recruitment company

We are looking for a Business Card Design that incorporates our personal details and our busines name and logo. We are a specialized search consultancy that recruit Property and Construction professionals.
We would like a business card that stands out and is appealing to the Construction and Property industry as well.

Target Market(s)

people in the construction and property industry

Contact Information for Business Card

Business Name and logo

Font styles to use
Serif

Colors
0094D4
00A9DD
6FCCEA
C7EBF8
E9F6FB

Requirements
Must have
• Business name and logo as well as contact details
Should not have
• No photos of us please

```html
<!DOCTYPE html>
<html lang="en">
<head>
<meta charset="utf-8">
<title>Maple Roster — Business Card</title>
<link href="https://fonts.googleapis.com/css2?family=Lora:wght@400;600&display=swap" rel="stylesheet">
<style>
  :root {
    --stage: #2b2d2f;
    --blue-deep: #0094d4;
    --blue-mid: #00a9dd;
    --blue-soft: #6fccea;
    --blue-pale: #c7ebf8;
    --blue-mist: #e9f6fb;
    --white: #ffffff;
    --grey: #4f5a61;
  }
  * { box-sizing: border-box; margin: 0; padding: 0; }
  html, body { width: 1200px; height: 1015px; overflow: hidden; }
  body {
    background: var(--stage);
    font-family: "Lora", Georgia, serif;
    position: relative;
  }
  .card {
    position: absolute;
    left: 280px;
    width: 640px;
    height: 366px;
    box-shadow: 0 10px 28px rgba(0,0,0,.45);
  }
  .card--front {
    top: 110px;
    background: var(--blue-deep);
    display: flex;
    align-items: center;
    justify-content: center;
  }
  .wordmark {
    color: var(--white);
    font-weight: 400;
    font-size: 50px;
    letter-spacing: 3px;
    text-transform: uppercase;
    white-space: nowrap;
  }
  .card--back {
    top: 540px;
    background: var(--white);
  }
  .accent-square {
    position: absolute;
    left: 40px;
    top: 122px;
    width: 50px;
    height: 50px;
    background: var(--blue-mid);
  }
  .person {
    position: absolute;
    left: 104px;
    top: 118px;
  }
  .person__name {
    color: var(--blue-deep);
    font-weight: 600;
    font-size: 24px;
    letter-spacing: .5px;
    text-transform: uppercase;
    line-height: 1.1;
    white-space: nowrap;
  }
  .person__role {
    color: var(--grey);
    font-size: 16px;
    margin-top: 2px;
  }
  .contact {
    position: absolute;
    left: 104px;
    top: 200px;
    list-style: none;
    font-size: 16px;
    color: var(--grey);
  }
  .contact li {
    display: flex;
    align-items: center;
    gap: 8px;
    height: 24px;
    white-space: nowrap;
  }
  .contact svg { width: 15px; height: 15px; fill: var(--blue-deep); flex: none; }
  .contact .contact__web { color: var(--blue-deep); }
  .address {
    position: absolute;
    left: 127px;
    top: 288px;
    font-size: 16px;
    line-height: 1.3;
    color: var(--grey);
    white-space: nowrap;
  }
  .brand {
    position: absolute;
    right: 44px;
    top: 0;
    height: 100%;
    display: flex;
    align-items: center;
  }
  .brand__name {
    color: var(--blue-deep);
    font-weight: 400;
    font-size: 24px;
    letter-spacing: 2px;
    text-transform: uppercase;
    white-space: nowrap;
  }
</style>
</head>
<body>
  <section class="card card--front">
    <span class="wordmark">Maple Roster</span>
  </section>

  <section class="card card--back">
    <div class="accent-square"></div>
    <div class="person">
      <div class="person__name">Daniel Hart</div>
      <div class="person__role">Managing Director</div>
    </div>
    <ul class="contact">
      <li>
        <svg viewBox="0 0 24 24" aria-hidden="true"><path d="M6.6 10.8a15.1 15.1 0 0 0 6.6 6.6l2.2-2.2a1 1 0 0 1 1-.25 11.4 11.4 0 0 0 3.6.57 1 1 0 0 1 1 1V20a1 1 0 0 1-1 1A17 17 0 0 1 3 4a1 1 0 0 1 1-1h3.5a1 1 0 0 1 1 1c0 1.25.2 2.45.57 3.57a1 1 0 0 1-.25 1z"/></svg>
        044-987 650 321
      </li>
      <li>
        <svg viewBox="0 0 24 24" aria-hidden="true"><path d="M2 5h20v14H2zm2 2v.5l8 5 8-5V7zm0 2.8V17h16V9.8l-8 5z"/></svg>
        info@mapleroster.com
      </li>
      <li class="contact__web">
        <svg viewBox="0 0 24 24" aria-hidden="true"><path d="M12 2a10 10 0 1 0 0 20 10 10 0 0 0 0-20zm6.9 6h-2.9a15.6 15.6 0 0 0-1.4-3.6A8 8 0 0 1 18.9 8zM12 4a14 14 0 0 1 1.9 4h-3.8A14 14 0 0 1 12 4zM4.3 14a8 8 0 0 1 0-4h3.4a16 16 0 0 0 0 4zm.8 2h2.9a15.6 15.6 0 0 0 1.4 3.6A8 8 0 0 1 5.1 16zM8 8H5.1a8 8 0 0 1 4.3-3.6A15.6 15.6 0 0 0 8 8zm4 12a14 14 0 0 1-1.9-4h3.8A14 14 0 0 1 12 20zm2.3-6H9.7a14.7 14.7 0 0 1 0-4h4.6a14.7 14.7 0 0 1 0 4zm.3 5.6A15.6 15.6 0 0 0 16 16h2.9a8 8 0 0 1-4.3 3.6zM16.3 14a16 16 0 0 0 0-4h3.4a8 8 0 0 1 0 4z"/></svg>
        www.mapleroster.com
      </li>
    </ul>
    <p class="address">421, Address line goes here<br>45452,Country Name</p>
    <div class="brand">
      <span class="brand__name">Maple Roster</span>
    </div>
  </section>
</body>
</html>
```